​Silver Harbor Rhythm provides personal, friendly service in a fun and high energy environment. We are based in Vermont.

We would like a card that appeals to a wide range of audiences as we do a wide range of events. Please feel free to check out our website silverharborrhythm.net for inspiration.

Target Market(s)

weddings, corporate, birthday parties, colleges

Industry/Entity Type

Business

Contact Information for Business Card

Silver Harbor Rhythm
Providing Entertainment For All Occasions
555 274 9160
silverharborrhythm@mailnest.net
silverharborrhythm.net

```html
<!DOCTYPE html>
<html lang="en">
<head>
<meta charset="utf-8">
<title>Silver Harbor Rhythm — Business Card</title>
<link rel="stylesheet" href="https://fonts.googleapis.com/css2?family=Questrial&family=Cormorant+SC:wght@600&display=swap">
<style>
  :root {
    --backdrop: #1c1c1c;
    --card-white: #ffffff;
    --card-black: #0c0c0c;
    --brand-green: #3e6a2f;
    --brand-red: #a8353a;
    --ink: #2a2a2a;
    --rule: #b9b9b9;
  }
  * { box-sizing: border-box; margin: 0; padding: 0; }
  html, body {
    width: 1200px; height: 871px; overflow: hidden;
    background: var(--backdrop);
  }
  .stage { position: relative; width: 1200px; height: 871px; }
  .card {
    position: absolute; left: 290px; width: 620px; height: 354px;
    border-radius: 3px;
  }
  .card--back { top: 60px; background: var(--card-black); }
  .card--front { top: 457px; background: var(--card-white); }

  .brand-name {
    font-family: "Questrial", sans-serif;
    color: var(--brand-green);
    font-size: 27px;
    letter-spacing: 0.5px;
    white-space: nowrap;
  }
  .card--back .brand-name {
    position: absolute; left: 0; right: 0; top: 156px;
    text-align: center; font-size: 34px;
  }
  .card--front .brand-name { position: absolute; left: 58px; top: 88px; }

  .divider {
    position: absolute; left: 45px; right: 45px; top: 186px;
    height: 1px; background: var(--rule);
  }
  .contacts {
    position: absolute; left: 58px; top: 208px; list-style: none;
    font-family: "Questrial", sans-serif; font-size: 13.5px; color: var(--ink);
  }
  .contacts li { display: flex; align-items: center; height: 28px; }
  .contacts svg { width: 15px; height: 15px; margin-right: 14px; flex: none; }

  .person {
    position: absolute; right: 45px; top: 236px; width: 170px; text-align: right;
  }
  .person__name {
    font-family: "Cormorant SC", serif; font-weight: 600;
    font-size: 17px; color: var(--brand-green); letter-spacing: 0.5px;
  }
  .person__rule { height: 1px; background: var(--rule); margin: 6px 0 5px; }
  .person__title {
    font-family: "Questrial", sans-serif; font-size: 10px; color: var(--brand-red);
  }
</style>
</head>
<body>
<main class="stage">
  <section class="card card--back" aria-label="Card back">
    <p class="brand-name">Silver Harbor Rhythm</p>
  </section>

  <section class="card card--front" aria-label="Card front">
    <p class="brand-name">Silver Harbor Rhythm</p>
    <div class="divider"></div>
    <ul class="contacts">
      <li>
        <svg viewBox="0 0 16 16" aria-hidden="true"><path d="M4 2l2.5 3-1.5 1.5c.8 1.8 2.2 3.2 4 4L10.5 9 13.5 11.5 12 14C6.5 13.5 2.5 9.5 2 4z" fill="var(--brand-green)"/></svg>
        555 274 9160
      </li>
      <li>
        <svg viewBox="0 0 16 16" aria-hidden="true"><rect x="1.5" y="3.5" width="13" height="9" fill="none" stroke="var(--brand-green)" stroke-width="1.6"/><path d="M1.5 3.5L8 9l6.5-5.5" fill="none" stroke="var(--brand-green)" stroke-width="1.6"/></svg>
        silverharborrhythm@mailnest.net
      </li>
      <li>
        <svg viewBox="0 0 16 16" aria-hidden="true"><circle cx="8" cy="8" r="6.3" fill="none" stroke="var(--brand-green)" stroke-width="1.6"/><ellipse cx="8" cy="8" rx="2.6" ry="6.3" fill="none" stroke="var(--brand-green)" stroke-width="1.3"/><path d="M1.7 8h12.6" stroke="var(--brand-green)" stroke-width="1.3"/></svg>
        silverharborrhythm.net
      </li>
    </ul>
    <div class="person">
      <p class="person__name">Dana Whitlock</p>
      <div class="person__rule"></div>
      <p class="person__title">CEO</p>
    </div>
  </section>
</main>
</body>
</html>
```